New Website Design for PHOVAN.org

We are looking for a new website design for PHOVAN.org. PHOVAN is a non profit home inspector association based in California. Home Inspectors are people that come out and look at a house before it's purchased to let the buyer know of any defects that may exist.
Our site is based on Joomla so if you'll be able to make a Joomla 3 template as well, please let us know (not required, but a bonus).
We would like to see designs that incorporate royal blue, white and chrome into the site as that's our main business colors.
We would like a place for rotating banners though they don't need to be the same size as the current site.
We would like navigation to be easier to manage with menus only across the top (via drop down menus) where we are going to sort out the items currently on the side. Possibly the front page could have a graphic link to separate portals for Realtors, Home Buyers and Inspectors, but that's just one option.
We would like a good mobile design or something that will scale easily to mobile.
The Find an Inspector feature is important and should stand out. The ASK PHOVANr site
Current home page feels a bit busy. Would like to simplify a bit.

```html
<!DOCTYPE html>
<html lang="en">
<head>
<meta charset="utf-8">
<title>PHOVAN – Pacific Home Inspection Association</title>
<link href="https://fonts.googleapis.com/css2?family=Ubuntu:wght@400;500;700&family=Open+Sans:wght@400;600&family=Kalam&display=swap" rel="stylesheet">
<style>
:root{
  --royal:#1d3f9a;
  --royal-dark:#16307a;
  --panel-blue:#2f6fd6;
  --ink:#333;
  --muted:#8c8c8c;
  --line:#d8d8d8;
  --dark:#2b2b2b;
  --darker:#1f1f1f;
  --white:#fff;
}
*{margin:0;padding:0;box-sizing:border-box}
html,body{width:830px;height:1200px;overflow:hidden}
body{position:relative;background:linear-gradient(#f1f1f1,#fff 160px);font-family:"Open Sans",Arial,sans-serif;color:var(--ink)}
.abs{position:absolute}
.top-rule{left:0;top:0;width:830px;height:2px;background:var(--royal)}
.brand{left:76px;top:30px;display:flex;align-items:center;gap:8px}
.brand-dot{width:34px;height:34px;border-radius:50%;background:var(--royal)}
.brand-name{font-family:"Ubuntu",sans-serif;font-weight:700;font-size:24px;color:var(--royal)}
.contact-tab{left:669px;top:0;width:85px;height:88px;background:var(--white);box-shadow:0 1px 3px rgba(0,0,0,.2)}
.contact-tab .tab-head{height:16px;background:var(--royal);color:#fff;font-family:"Ubuntu",sans-serif;font-size:11px;line-height:16px;padding-left:8px}
.contact-tab .phone{font-family:"Kalam",cursive;color:var(--royal);font-size:10.5px;line-height:12px;padding:34px 0 0 5px}
.email{left:496px;top:40px;font-style:italic;color:var(--royal);font-size:11px}
.search{left:522px;top:62px;width:130px;height:21px;border:1px solid var(--line);background:#fff;font-size:9px;color:#bbb;padding:5px 7px}
.search svg{position:absolute;right:4px;top:4px}
.search:after{content:"";position:absolute;right:25px;top:3px;width:1px;height:14px;background:var(--line)}
.nav{left:0;top:95px;font-family:"Ubuntu",sans-serif;font-size:10px;color:#555}
.nav span{position:absolute;top:4px;white-space:nowrap}
.nav .active{left:242px;top:0;width:42px;height:19px;background:var(--royal);color:#fff;border-radius:2px;text-align:center;line-height:19px;font-size:10.5px}
.hero{left:76px;top:149px;width:678px;height:297px;border-radius:10px 10px 0 0;overflow:hidden;background:linear-gradient(100deg,#ece9e4 0%,#c9c2b8 28%,#8a2a2a 42%,#9b3030 60%,#e8e8e8 75%,#5b6066 100%)}
.hero-band{left:0;top:243px;width:678px;height:54px;background:#232323}
.hero-caption{left:350px;top:221px;width:328px;height:76px;background:#1f1f1f;clip-path:polygon(14px 0,100% 0,100% 100%,0 100%,0 26px)}
.hero-caption h1{position:absolute;left:20px;top:9px;font-family:"Ubuntu",sans-serif;font-size:16px;color:#fff;font-weight:500}
.hero-caption p{position:absolute;left:20px;top:32px;width:300px;font-size:8.2px;line-height:10.5px;color:#fff}
.dots{left:10px;top:12px;display:flex;gap:4px}
.dots i{width:9px;height:3px;background:#fff}
.dots i.off{background:var(--royal)}
.finder{left:0;top:157px;width:178px;height:86px;background:var(--panel-blue);border-radius:0 6px 0 0}
.field{position:absolute;height:18px;border:1px solid #cfe0ff;background:#234a93;color:#fff;font-size:9px;line-height:16px;padding-left:6px}
.finder .go{position:absolute;left:14px;top:71px;color:#fff;font-size:9px;display:flex;align-items:center;gap:6px}
.quick{position:absolute;top:262px;color:#fff;font-family:"Ubuntu",sans-serif;font-size:9px;line-height:11px;display:flex;gap:8px;align-items:center}
.arrow{font-size:34px;color:#888;font-weight:300;top:272px}
.hero-shadow{left:76px;top:446px;width:678px;height:18px;background:linear-gradient(#e2e2e2,rgba(255,255,255,0));border-radius:0 0 50% 50%}
.hr{left:0;width:830px;height:1px;background:var(--line)}
.card{width:146px;top:506px}
.card .pic{height:84px;position:relative;overflow:hidden}
.card .cap{position:absolute;left:0;bottom:0;width:100%;height:22px;background:rgba(20,20,20,.85);color:#fff;font-size:9px;line-height:22px;padding-left:6px}
.card p{padding:12px 7px 0;font-size:8.2px;line-height:12.5px;color:var(--muted)}
.gal-head{left:86px;top:681px;font-family:"Ubuntu",sans-serif;font-weight:500;font-size:12px;color:var(--royal);display:flex;align-items:center;gap:6px}
.gal-head i{width:10px;height:10px;background:var(--royal)}
.gal-frame{left:86px;top:701px;width:443px;height:144px;border:1px solid var(--line);background:#fff}
.shot{position:absolute}
.gal-text{left:86px;top:860px;width:445px;font-size:8.8px;line-height:13px;color:#555}
.social{left:556px;top:698px;width:194px;height:64px;background:var(--royal)}
.social small{position:absolute;left:11px;top:10px;font-size:8px;color:#9fb6e8}
.social b{position:absolute;left:11px;top:22px;font-family:"Ubuntu",sans-serif;font-size:20px;color:#fff;font-weight:700}
.social .like{position:absolute;left:136px;top:23px;width:46px;height:14px;background:#eef2fa;color:var(--royal);font-size:7.5px;line-height:14px;text-align:center}
.assoc{left:556px;top:786px;width:194px;height:77px;border:1px solid var(--line);background:#fff}
.assoc h3{position:absolute;left:11px;top:11px;font-family:"Ubuntu",sans-serif;font-weight:400;font-size:10.5px;line-height:13px;color:#333}
.assoc .seal{position:absolute;left:127px;top:8px;width:56px;height:56px;border-radius:50%;background:#c9c9c9}
.assoc a{position:absolute;left:13px;top:60px;font-size:8px;color:#333;text-decoration:underline}
.box-shadow{height:12px;background:linear-gradient(rgba(0,0,0,.12),rgba(0,0,0,0));border-radius:0 0 50% 50%}
.footer{left:0;top:908px;width:830px;height:252px;background:var(--dark);border-top:4px solid #555}
.legal{left:0;top:1160px;width:830px;height:40px;background:var(--darker);font-size:8px;color:#aaa;padding:14px 0 0 86px}
.legal b{color:#eee;font-weight:400}
.f-head{top:928px;font-family:"Ubuntu",sans-serif;font-size:11.5px;color:#fff}
.news{left:86px;width:200px;height:40px}
.news .thumb{position:absolute;left:0;top:0;width:40px;height:40px;border:1px solid #555}
.news h4{position:absolute;left:50px;top:2px;font-family:"Ubuntu",sans-serif;font-weight:400;font-size:10.5px;color:#fff}
.news p{position:absolute;left:51px;top:17px;width:150px;font-family:Arial,sans-serif;font-size:7.3px;line-height:11px;color:#bbb}
.tweet{left:302px;width:144px;font-family:Arial,sans-serif;font-size:8px;line-height:14px;color:#aaa}
.tweet b{color:#fff;font-weight:400}
.ago{left:302px;font-family:Arial,sans-serif;font-size:8px;color:#fff;display:flex;gap:5px;align-items:center}
.rule{left:302px;width:144px;height:1px;background:#555}
.popular{left:468px;top:960px;list-style:none;font-family:"Ubuntu",sans-serif;font-size:8.8px;color:#fff}
.popular li{height:22.6px;padding-left:10px;position:relative}
.popular li:before{content:"";position:absolute;left:0;top:3px;border-left:4px solid #fff;border-top:3px solid transparent;border-bottom:3px solid transparent}
.ft{width:43px;height:43px;border:1px solid #555}
</style>
</head>
<body>
<div class="abs top-rule"></div>

<div class="abs brand"><span class="brand-dot"></span><span class="brand-name">PHOVAN</span></div>

<div class="abs email">mailto:Webmaster@PHOVAN.ORG</div>
<div class="abs search">Search
  <svg width="13" height="13" viewBox="0 0 13 13"><circle cx="5.5" cy="5.5" r="4" fill="none" stroke="#666" stroke-width="1.6"/><line x1="8.5" y1="8.5" x2="12" y2="12" stroke="#666" stroke-width="1.8"/></svg>
</div>
<div class="abs contact-tab">
  <div class="tab-head">Contact Us ▾</div>
  <div class="phone">(800) 555-0142<br>(916) 555-0187</div>
</div>

<nav class="abs nav">
  <span class="active">HOME</span>
  <span style="left:296px">Find an Inspector</span>
  <span style="left:384px">Home Buyers &amp; Sellers</span>
  <span style="left:496px">Real Estate Agents</span>
  <span style="left:589px">Inspectors</span>
  <span style="left:648px">Ask Phovan</span>
  <span style="left:703px">Conferences</span>
</nav>

<div class="abs arrow" style="left:36px">〈</div>
<div class="abs arrow" style="left:766px">〉</div>

<section class="abs hero" role="img" aria-label="Banner photo: inspector reviewing house plans in front of a red building">
  <div class="abs dots"><i></i><i></i><i></i><i class="off"></i></div>
  <div class="abs hero-band"></div>
  <div class="abs hero-caption">
    <h1>Welcome to PHOVAN</h1>
    <p>The Pacific Home Inspection Association (PHOVAN) is a voluntary, nonprofit public-benefit organization of real estate inspectors.</p>
  </div>
  <div class="abs finder">
    <div class="field" style="left:11px;top:16px;width:151px">Distance<span style="position:absolute;right:8px;top:0">▾</span></div>
    <div class="field" style="left:11px;top:41px;width:73px">From</div>
    <div class="field" style="left:89px;top:41px;width:73px">To</div>
    <div class="go">
      <svg width="16" height="16" viewBox="0 0 16 16"><rect x="1" y="1" width="12" height="12" fill="none" stroke="#fff"/><circle cx="7" cy="7" r="3.5" fill="none" stroke="#fff" stroke-width="1.5"/><line x1="9.5" y1="9.5" x2="14" y2="14" stroke="#fff" stroke-width="2"/></svg>
      SEARCH NOW</div>
  </div>
  <div class="quick" style="left:14px">
    <svg width="26" height="26" viewBox="0 0 26 26"><rect width="26" height="26" rx="3" fill="#3a7be0"/><path d="M8 20V7l10 4-10 4" fill="#fff"/></svg>
    <span>SEARCH FOR<br>INSPECTOR</span></div>
  <div class="quick" style="left:134px">
    <svg width="22" height="24" viewBox="0 0 22 24"><rect x="1" y="1" width="20" height="22" fill="none" stroke="#fff" stroke-width="1.5"/><path d="M4 6h14M4 10h14M4 14h14M4 18h14" stroke="#fff" stroke-width="1.5"/></svg>
    <span>INSPECTOR<br>LOGIN</span></div>
  <div class="quick" style="left:246px">
    <svg width="22" height="22" viewBox="0 0 22 22"><rect x="2" y="4" width="18" height="14" rx="3" fill="none" stroke="#fff" stroke-width="1.5"/><path d="M7 11l3 3 5-6" fill="none" stroke="#fff" stroke-width="1.5"/></svg>
    <span>UP COMMING<br>EVENTS</span></div>
</section>
<div class="abs hero-shadow"></div>
<div class="abs hr" style="top:478px"></div>

<article class="abs card" style="left:83px">
  <div class="pic" role="img" aria-label="Sunlit forest path" style="background:linear-gradient(#6fae3a,#2f6a1f)"><div class="cap">Path to Success Program</div></div>
  <p>Duis aute irure dolor reprehenderit in voluptate velit esse cillum dolore eu fugiat nulla pariatur. Excepteur sint occaecat cupidatat.</p>
</article>
<article class="abs card" style="left:256px">
  <div class="pic" role="img" aria-label="Raised hand in front of a green board" style="background:linear-gradient(#3d8a5e,#1f5a3a)"><div class="cap">Educational Publications</div></div>
  <p>Lorem ipsum dolor sit consectetur adipisicing elit amet sid do eiusmod tempor incididunt labore sint occaecat.</p>
</article>
<article class="abs card" style="left:429px">
  <div class="pic" role="img" aria-label="New construction specialist badge" style="background:#fafafa;border:1px solid #ddd"><div class="cap">Phovan New Construction</div></div>
  <p>Duis aute irure dolor reprehenderit in voluptate velit esse cillum dolore eu fugiat nulla pariatur. Excepteur sint occaecat cupidatat.</p>
</article>
<article class="abs card" style="left:602px">
  <div class="pic" role="img" aria-label="Grey two-storey house" style="background:linear-gradient(#d6d6d6,#6a6a6a)"><div class="cap">PHOVAN Press / Media Archives</div></div>
  <p>Duis aute irure dolor reprehenderit in voluptate velit esse cillum dolore eu fugiat nulla pariatur. Excepteur sint occaecat cupidatat.</p>
</article>

<div class="abs hr" style="top:670px;left:83px;width:666px;background:#eee"></div>

<h2 class="abs gal-head"><i></i>GALLERY</h2>
<div class="abs gal-frame">
  <div class="shot" role="img" aria-label="Woman reading in a blue chair" style="left:3px;top:3px;width:129px;height:66px;background:linear-gradient(#e8e8e8,#3a5fc0)"></div>
  <div class="shot" role="img" aria-label="Glass skylight roof" style="left:3px;top:75px;width:129px;height:66px;background:linear-gradient(#cfe3ef,#6fa0bf)"></div>
  <div class="shot" role="img" aria-label="Man at an office window over the city" style="left:135px;top:3px;width:131px;height:138px;background:linear-gradient(90deg,#3a3a3a,#c8ccd0 40%,#aab0b6)"></div>
  <div class="shot" role="img" aria-label="Striped building facade" style="left:303px;top:3px;width:136px;height:67px;background:repeating-linear-gradient(#9a9a9a 0 3px,#e0e0e0 3px 6px)"></div>
  <div class="shot" role="img" aria-label="Woman with laptop in airport seating" style="left:303px;top:72px;width:136px;height:69px;background:linear-gradient(#f4f4f4,#6a6a6a)"></div>
</div>
<p class="abs gal-text">El aluminio es un metal que se distingue de otros materiales por su propiedades tecnológicas. Su ligereza y su resistencia mecánica, lo hacen útil para múltiples y exigentes aplicaciones, ya que su densidad es un</p>

<div class="abs social"><small>Pacific Home Inspection</small><b>Connectly</b><span class="like">👍 Like</span></div>
<div class="abs box-shadow" style="left:556px;top:762px;width:194px"></div>
<div class="abs assoc">
  <h3>Pacific Home<br>Inspection Association</h3>
  <span class="seal"></span>
  <a>Read More</a>
</div>
<div class="abs box-shadow" style="left:556px;top:863px;width:194px"></div>

<footer class="abs footer"></footer>
<h3 class="abs f-head" style="left:85px">Latest News</h3>
<h3 class="abs f-head" style="left:302px">Latest Tweets</h3>
<h3 class="abs f-head" style="left:481px">Popular</h3>
<h3 class="abs f-head" style="left:602px">Gallery</h3>

<div class="abs news" style="top:962px"><span class="thumb" role="img" aria-label="Restaurant table" style="background:linear-gradient(#7a3a2a,#e0c0a0)"></span><h4>Schedule</h4><p>Lorem ipsum dolor amet laboris consectetur adipisicing elit,</p></div>
<div class="abs news" style="top:1012px"><span class="thumb" role="img" aria-label="Couple outdoors" style="background:linear-gradient(#6a8a5a,#c0b090)"></span><h4>Confrence Schedule</h4><p>Lorem ipsum dolor amet laboris consectetur adipisicing elit,</p></div>
<div class="abs news" style="top:1063px"><span class="thumb" role="img" aria-label="Fire scene" style="background:linear-gradient(#e06a1a,#5a7aa0)"></span><h4>General Information</h4><p>Lorem ipsum dolor amet laboris consectetur adipisicing elit,</p></div>

<p class="abs tweet" style="top:961px">Burger Barn goes abstract with crowd-sourced animations: <b>http://sh.example /tEe0ZrvIJp</b></p>
<div class="abs ago" style="top:1018px"><svg width="9" height="9" viewBox="0 0 9 9"><circle cx="4.5" cy="4.5" r="3.7" fill="none" stroke="#fff" stroke-width="1.2"/><path d="M4.5 2.5v2h1.5" stroke="#fff" fill="none"/></svg>34 mins ago</div>
<div class="abs rule" style="top:1038px"></div>
<p class="abs tweet" style="top:1046px">"CSV to SiteForge Import" useable especially for directory siteforge theme <b>http://sh.example/Ps7gVgDWJx #siteforge #plugin</b></p>
<div class="abs ago" style="top:1116px"><svg width="9" height="9" viewBox="0 0 9 9"><circle cx="4.5" cy="4.5" r="3.7" fill="none" stroke="#fff" stroke-width="1.2"/><path d="M4.5 2.5v2h1.5" stroke="#fff" fill="none"/></svg>1 hour ago</div>
<div class="abs rule" style="top:1136px"></div>

<ul class="abs popular">
  <li>Inspection FAQs</li><li>Common Venting of Gas</li><li>Becoming a Member</li><li>Education / CECs</li><li>Affiliate Directory</li><li>Lorem Lipsum</li>
</ul>

<div class="abs ft" role="img" aria-label="Concert stage" style="left:606px;top:962px;background:linear-gradient(#2a3a6a,#0a0a1a)"></div>
<div class="abs ft" role="img" aria-label="Blue and white artwork" style="left:653px;top:962px;background:linear-gradient(90deg,#2a4ad0,#eee)"></div>
<div class="abs ft" role="img" aria-label="Evening fire" style="left:701px;top:962px;background:linear-gradient(#1a1010,#8a3a2a)"></div>
<div class="abs ft" role="img" aria-label="Sunset crowd" style="left:606px;top:1010px;background:linear-gradient(#e0a060,#5a3a2a)"></div>
<div class="abs ft" role="img" aria-label="Glowing light" style="left:653px;top:1010px;background:radial-gradient(#f0a040,#2a1a10)"></div>
<div class="abs ft" role="img" aria-label="Outdoor field" style="left:701px;top:1010px;background:linear-gradient(#c08060,#6a7a3a)"></div>
<div class="abs ft" role="img" aria-label="Dim room" style="left:606px;top:1058px;background:linear-gradient(#6a5030,#1a1208)"></div>
<div class="abs ft" role="img" aria-label="Stage performance" style="left:653px;top:1058px;background:linear-gradient(#3a3a3a,#0a0a0a)"></div>
<div class="abs ft" role="img" aria-label="Party lights" style="left:701px;top:1058px;background:linear-gradient(#c0c0c0,#3a2a2a)"></div>

<div class="abs legal">© 2012 Copyright by <b>Real Estate</b> &nbsp; All rights reserved.</div>
</body>
</html>
```